Velvet Dice Night Age Verification Landing Page

To create a visually appealing design for the landing page of the adult game "Velvet Dice Night" that confirms the visitor's age.
The design should have a simple and visually appealing look that focuses on two buttons labeled "Yes" and "No". The purpose of the page is to confirm that the visitor is 18 years of age or older before accessing the game's content. Responsive design that works well on desktop and mobile devices. The final output should be delivered in PSD, AI, or Sketch format, along with any necessary images or assets.
I have also attached examples.

```html
<!DOCTYPE html>
<html lang="en">
<head>
<meta charset="utf-8">
<title>Velvet Dice Night — Age Verification</title>
<link rel="stylesheet" href="https://fonts.googleapis.com/css2?family=Poppins:wght@400;500;600&display=swap">
<style>
  :root {
    --page: #ffffff;
    --card-fill: rgba(8, 6, 8, 0.78);
    --card-line: #bdbbbd;
    --brand: #9b63b3;
    --yes: #7d5a97;
    --no: #3b3b3e;
    --ink: #ffffff;
  }
  * { margin: 0; padding: 0; box-sizing: border-box; }
  html, body { width: 973px; height: 1200px; overflow: hidden; background: var(--page); }
  body { position: relative; font-family: "Poppins", sans-serif; color: var(--ink); }

  .screen {
    position: absolute;
    left: 35px;
    width: 903px;
    height: 556px;
    overflow: hidden;
  }
  .screen--first { top: 35px; }
  .screen--second { top: 608px; }

  .screen__photo { position: absolute; inset: 0; }
  .screen--first .screen__photo {
    background:
      radial-gradient(ellipse 30% 55% at 50% 40%, rgba(120, 96, 78, 0.55), transparent 70%),
      linear-gradient(180deg, #2a1a18 0%, #1e1413 55%, #141010 100%);
  }
  .screen--second .screen__photo {
    background:
      radial-gradient(ellipse 42% 45% at 50% 35%, rgba(92, 66, 60, 0.7), transparent 75%),
      linear-gradient(180deg, #2e2220 0%, #221816 60%, #1a1212 100%);
  }

  .verify-card {
    position: absolute;
    left: 261px;
    top: 213px;
    width: 384px;
    height: 193px;
  }
  .verify-card__fill {
    position: absolute;
    inset: 0;
    border-radius: 24px;
    background: var(--card-fill);
  }
  .verify-card__frame { position: absolute; inset: 0; overflow: visible; }

  .brand-name {
    position: absolute;
    left: 0;
    right: 0;
    top: -15px;
    text-align: center;
    font-size: 20px;
    font-weight: 600;
    line-height: 30px;
    color: var(--brand);
    letter-spacing: 0.2px;
  }

  .verify-card__question {
    position: absolute;
    left: 0;
    right: 0;
    top: 62px;
    text-align: center;
    font-size: 19.5px;
    font-weight: 400;
    letter-spacing: 0.3px;
  }

  .answer {
    position: absolute;
    top: 102px;
    width: 129px;
    height: 38px;
    border-radius: 19px;
    font-size: 14px;
    font-weight: 600;
    line-height: 38px;
    text-align: center;
    letter-spacing: 0.4px;
  }
  .answer--yes { left: 57px; background: var(--yes); }
  .answer--no { left: 198px; background: var(--no); }

  .remember {
    position: absolute;
    left: 0;
    right: 0;
    top: 157px;
    display: flex;
    justify-content: center;
    align-items: center;
    gap: 7px;
    font-size: 10.5px;
    font-weight: 600;
    letter-spacing: 0.2px;
  }
  .remember__box {
    width: 9px;
    height: 9px;
    border: 1.3px solid var(--ink);
    border-radius: 1px;
  }
</style>
</head>
<body>

  <section class="screen screen--first">
    <div class="screen__photo" role="img" aria-label="Dimmed photo of a model in a black mask and lingerie posed on a dark leather sofa before a brick wall"></div>
    <div class="verify-card">
      <div class="verify-card__fill"></div>
      <svg class="verify-card__frame" width="384" height="193" viewBox="0 0 384 193" aria-hidden="true">
        <path d="M92 1.5 H25 A23.5 23.5 0 0 0 1.5 25 V168 A23.5 23.5 0 0 0 25 191.5 H359 A23.5 23.5 0 0 0 382.5 168 V25 A23.5 23.5 0 0 0 359 1.5 H292" fill="none" stroke="var(--card-line)" stroke-width="2.2"/>
      </svg>
      <div class="brand-name">Velvet Dice Night</div>
      <p class="verify-card__question">Are You Over 18 Years of Age?</p>
      <div class="answer answer--yes">Yes</div>
      <div class="answer answer--no">Now</div>
      <div class="remember"><span class="remember__box"></span><span>Remember Me</span></div>
    </div>
  </section>

  <section class="screen screen--second">
    <div class="screen__photo" role="img" aria-label="Dimmed close-up photo of a model from behind in black lace lingerie and stockings"></div>
    <div class="verify-card">
      <div class="verify-card__fill"></div>
      <svg class="verify-card__frame" width="384" height="193" viewBox="0 0 384 193" aria-hidden="true">
        <path d="M92 1.5 H25 A23.5 23.5 0 0 0 1.5 25 V168 A23.5 23.5 0 0 0 25 191.5 H359 A23.5 23.5 0 0 0 382.5 168 V25 A23.5 23.5 0 0 0 359 1.5 H292" fill="none" stroke="var(--card-line)" stroke-width="2.2"/>
      </svg>
      <div class="brand-name">Velvet Dice Night</div>
      <p class="verify-card__question">Are You Over 18 Years of Age?</p>
      <div class="answer answer--yes">Yes</div>
      <div class="answer answer--no">Now</div>
      <div class="remember"><span class="remember__box"></span><span>Remember Me</span></div>
    </div>
  </section>

</body>
</html>
```